Business Card Design for Occupational Medicine Start Up Company

We need to design a professional business card. We are a healthcare company providing occupational medicine services to blue collar industries. We are professional, efficient and high quality service providers.

Target Market(s)

Blue Collar Industry: Shipbuilding, Ports, Trucking Companies; The Executives and Safety Officers for these companies

Industry/Entity Type

Healthcare

Contact Information for Business Card

Logo, Name, Title, Email, Phone

Other font styles liked:
• Please match our Brand Guide

Requirements
Must have
• Our Company Colors and Logo

```html
<!DOCTYPE html>
<html lang="en">
<head>
<meta charset="utf-8">
<title>CrewWell Clinics – Business Card</title>
<link rel="stylesheet" href="https://fonts.googleapis.com/css2?family=Montserrat:wght@400;500;600;700&display=swap">
<style>
  :root {
    --navy: #2b3580;
    --sky: #29a8e0;
    --orange: #f4b04f;
    --ink: #4a4a52;
    --paper: #ffffff;
    --backdrop: #e4e4e4;
  }
  * { margin: 0; padding: 0; box-sizing: border-box; }
  html, body {
    width: 1200px; height: 588px; overflow: hidden;
    background: var(--backdrop);
    font-family: "Montserrat", sans-serif;
  }
  .canvas { position: relative; width: 1200px; height: 588px; }

  .card {
    position: absolute;
    width: 488px; height: 287px;
    border-radius: 18px;
    overflow: hidden;
  }
  .card--front { left: 87px; top: 141px; background: var(--paper); }
  .card--back { left: 622px; top: 143px; background: var(--navy); }

  /* front */
  .brand {
    position: absolute; left: 28px; top: 30px;
    display: flex; align-items: center; gap: 14px;
  }
  .brand__dot {
    width: 40px; height: 40px; border-radius: 50%;
    background: var(--navy);
  }
  .brand__name {
    color: var(--navy); font-weight: 700;
    line-height: 1;
  }
  .brand__name .line1 { display: block; font-size: 20px; letter-spacing: 0.2px; }
  .brand__name .line2 { display: block; font-size: 11px; letter-spacing: 4.5px; margin-top: 4px; text-align: center; }

  .accent-tab {
    position: absolute; left: 0; top: 138px;
    width: 9px; height: 32px;
    background: var(--orange);
    border-radius: 0 5px 5px 0;
  }
  .person { position: absolute; left: 26px; top: 136px; }
  .person__name { color: var(--navy); font-size: 17px; font-weight: 700; letter-spacing: 0.2px; }
  .person__title { color: var(--ink); font-size: 13px; font-weight: 400; margin-top: 4px; }

  .contacts { position: absolute; left: 27px; top: 202px; list-style: none; }
  .contacts li {
    display: flex; align-items: center; gap: 6px;
    color: var(--ink); font-size: 12.5px; height: 19.5px;
  }
  .contacts svg { width: 11px; height: 11px; fill: var(--sky); flex: none; }

  .decor {
    position: absolute; top: 0; height: 100%;
  }
  .card--front .decor {
    right: 0; width: 145px;
    background: linear-gradient(160deg, var(--orange) 0%, var(--navy) 40%, var(--sky) 70%, var(--navy) 100%);
    border-radius: 70px 0 0 70px;
  }
  .card--back .decor {
    left: 0; width: 145px;
    background: linear-gradient(200deg, var(--orange) 0%, var(--paper) 30%, var(--sky) 55%, var(--paper) 80%, var(--orange) 100%);
    border-radius: 0 70px 70px 0;
  }

  /* back */
  .back-brand {
    position: absolute; left: 190px; top: 128px; width: 270px;
    color: var(--paper); font-weight: 700; text-align: center; line-height: 1;
  }
  .back-brand .line1 { display: block; font-size: 28px; letter-spacing: 0.3px; }
  .back-brand .line2 { display: block; font-size: 15px; letter-spacing: 6px; margin-top: 6px; }
</style>
</head>
<body>
<main class="canvas">

  <section class="card card--front" aria-label="Business card front">
    <div class="brand">
      <span class="brand__dot"></span>
      <span class="brand__name"><span class="line1">CREWWELL</span><span class="line2">CLINICS</span></span>
    </div>

    <span class="accent-tab"></span>

    <div class="person">
      <p class="person__name">MARK ELLISON</p>
      <p class="person__title">President</p>
    </div>

    <ul class="contacts">
      <li>
        <svg viewBox="0 0 24 24" aria-hidden="true"><path d="M6.6 10.8a15.1 15.1 0 0 0 6.6 6.6l2.2-2.2c.3-.3.7-.4 1-.2 1.1.4 2.3.6 3.6.6.6 0 1 .4 1 1V20c0 .6-.4 1-1 1A17 17 0 0 1 3 4c0-.6.4-1 1-1h3.5c.6 0 1 .4 1 1 0 1.3.2 2.5.6 3.6.1.3 0 .7-.2 1z"/></svg>
        555-014-2290
      </li>
      <li>
        <svg viewBox="0 0 24 24" aria-hidden="true"><path d="M2 5h20v14H2z" opacity=".9"/><path d="M2 5l10 8 10-8" fill="none" stroke="#fff" stroke-width="2"/></svg>
        mark@crewwellclinics.com
      </li>
      <li>
        <svg viewBox="0 0 24 24" aria-hidden="true"><circle cx="12" cy="12" r="10"/><path d="M2 12h20M12 2c3 3 3 17 0 20M12 2c-3 3-3 17 0 20" fill="none" stroke="#fff" stroke-width="1.5"/></svg>
        www.crewwellclinics.com
      </li>
    </ul>

    <div class="decor" role="img" aria-label="Large brand symbol decoration in navy, sky blue and orange"></div>
  </section>

  <section class="card card--back" aria-label="Business card back">
    <div class="decor" role="img" aria-label="Large brand symbol decoration in white, sky blue and orange"></div>
    <p class="back-brand"><span class="line1">CREWWELL</span><span class="line2">CLINICS</span></p>
  </section>

</main>
</body>
</html>
```